Stationery Design Project for Marketing Consultancy

I have started a new consultancy business and require the following elements to be designed using existing logo:
• Business card
• Letterhead
• Envelope (DL, C4, C5)
• Microsoft word template for report writing
• A4 Presentation Folder
• Powerpoint template
COPY FOR FRONT AND BACK OF BUSINESS CARD
logo
'Measurable Marketing. Epic Results' slogan (but no need to use existing lockup with logo)
name, B Bus. Mktg, Grad Dip Digital Mktg, CPM (post nominal abbreviations in smaller font)
mobile: 04XX-XXX-XXX (I will give details to the winner to add)
website: www.tolvarin.com.au
email: info@tolvarin.com.au
COPY FOR LETTERHEAD
Logo
Company Name
Please, submit your designs that include business card, letterhead and envelope. Once selected the winner will be asked to complete the project by creating the rest of the artwork.
FINAL FILES
Print ready files to be supplied as well as Indesign files so that minor amends can be made if necessary in future.
• Layered vectors in EPS & PDF
• Screen quality JPEG & PNGs
ABOUT THE BUSINESS: TOLVARIN
I work with clients to understand their business challenges, developing and executing measurable marketing strategies tied to key business metrics. Services include:
Services include:
• Business planning and business development
• Marketing and brand strategy
• Insight-driven integrated campaigns
• Loyalty programs and retention marketing
• Marketing automation
• Direct marketing (traditional and digital)
• Content strategy and development
Hi everyone,
Target Market(s)
Corporate decision makers (heads of marketing, general managers etc) and small to medium sized business owners. Predominately male aged 35+
Industry/Entity Type
Marketing
Requirements
Must have
- BRAND PERSONALITY
The successful design will communicate brand personality. I am a professional, results-driven entrepreneur, but want to show off my creative flair.
MEMORABILITY
Looking for a unique and eye-catching design. Am considering special printing effects (die cuts, letterpress, interactive elements, embossing, foiling etc) or a striking minimalist approach.
Nice to have
- I have a mission that could be incorporated on reverse if room -
Turning insights into actions & passion into profit.
Should not have
- Use of pink or green.

```html
<!DOCTYPE html>
<html lang="en">
<head>
<meta charset="utf-8">
<title>Tolvarin Stationery Set</title>
<link href="https://fonts.googleapis.com/css2?family=Open+Sans:wght@400;600;700;800&display=swap" rel="stylesheet">
<style>
  :root {
    --ink: #000000;
    --paper: #ffffff;
    --mark-grey: #3a3a3a;
    --watermark: #e4e4e4;
    --text-dark: #222222;
    --text-light: #ffffff;
    --rule: #999999;
    --backdrop-light: #f4f4f4;
    --backdrop-mid: #a9a9a9;
    --backdrop-dark: #3c3c3c;
  }
  * { margin: 0; padding: 0; box-sizing: border-box; }
  html, body { width: 1200px; height: 1143px; overflow: hidden; }
  body {
    position: relative;
    font-family: "Open Sans", Arial, sans-serif;
    background: linear-gradient(135deg, var(--backdrop-light) 0%, var(--backdrop-mid) 55%, var(--backdrop-dark) 100%);
    color: var(--text-dark);
  }
  .piece { position: absolute; box-shadow: 3px 4px 8px rgba(0,0,0,0.35); }
  .brand-name { font-weight: 800; letter-spacing: 0.02em; text-transform: uppercase; white-space: nowrap; }
  .brand-dot { position: absolute; border-radius: 50%; }
  .slogan { font-weight: 600; text-transform: uppercase; white-space: nowrap; letter-spacing: 0.02em; }

  /* Business cards */
  .card { width: 138px; height: 93px; background: var(--ink); color: var(--text-light); }
  .card-front { left: 194px; top: 208px; }
  .card-back { left: 351px; top: 208px; }
  .card-front .brand-dot { left: 53px; top: 18px; width: 30px; height: 30px; background: var(--text-light); }
  .card-front .brand-name { position: absolute; left: 0; right: 0; top: 54px; text-align: center; font-size: 13px; }
  .card-front .slogan { position: absolute; left: 0; right: 0; top: 72px; text-align: center; font-size: 4.5px; }
  .card-back .brand-dot { left: 112px; top: 10px; width: 14px; height: 14px; background: var(--text-light); }
  .card-back .contact { position: absolute; left: 28px; top: 30px; font-size: 5px; line-height: 1.5; }
  .card-back .contact .company { font-weight: 700; font-size: 6.5px; margin-bottom: 5px; }
  .card-back .contact .web { font-weight: 700; margin-top: 2px; }

  /* DL envelope */
  .envelope-dl { left: 621px; top: 150px; width: 405px; height: 194px; background: var(--paper); }
  .envelope-dl .brand-dot { left: 31px; top: 11px; width: 24px; height: 24px; background: var(--mark-grey); }
  .envelope-dl .brand-name { position: absolute; left: 22px; top: 40px; font-size: 9px; color: var(--mark-grey); }
  .envelope-dl .slogan { position: absolute; left: 22px; top: 52px; font-size: 3.5px; color: var(--mark-grey); }

  /* Footer line shared by letterhead and DL */
  .contact-line { position: absolute; display: flex; align-items: center; font-size: 7px; white-space: nowrap; color: var(--text-dark); }
  .contact-line span { padding: 0 5px; border-left: 1px solid var(--rule); }
  .contact-line span:first-child { border-left: none; padding-left: 0; font-weight: 700; }
  .contact-line span.web { font-weight: 700; }
  .envelope-dl .contact-line { left: 69px; top: 177px; }

  /* Letterhead */
  .letterhead { left: 188px; top: 375px; width: 379px; height: 505px; background: var(--paper); }
  .letterhead .brand-dot { left: 35px; top: 15px; width: 40px; height: 40px; background: var(--mark-grey); }
  .letterhead .brand-name { position: absolute; left: 20px; top: 62px; font-size: 15px; color: var(--mark-grey); }
  .letterhead .slogan { position: absolute; left: 20px; top: 82px; font-size: 4.5px; color: var(--mark-grey); }
  .letterhead .watermark { position: absolute; left: 88px; top: 160px; width: 190px; height: 190px; border-radius: 50%; background: var(--watermark); }
  .letterhead .contact-line { left: 40px; top: 481px; }

  /* C4 envelope */
  .envelope-c4 { left: 619px; top: 375px; width: 417px; height: 655px; background: var(--paper); }
  .envelope-c4 .flap { position: absolute; left: 0; top: 0; width: 417px; height: 120px; }
  .envelope-c4 .flap .brand-dot { left: 178px; top: 18px; width: 44px; height: 44px; background: var(--text-light); }
  .envelope-c4 .flap .brand-name { position: absolute; left: 0; right: 0; top: 68px; text-align: center; font-size: 17px; color: var(--text-light); }
  .envelope-c4 .flap .slogan { position: absolute; left: 0; right: 0; top: 92px; text-align: center; font-size: 5.5px; color: var(--text-light); }
  .envelope-c4 .side-mark { position: absolute; left: 29px; top: 503px; width: 58px; height: 58px; border-radius: 50%; background: var(--mark-grey); }
  .envelope-c4 .side-lockup { position: absolute; left: 102px; top: 611px; transform: rotate(-90deg); transform-origin: 0 0; }
  .envelope-c4 .side-lockup .brand-name { font-size: 24px; line-height: 1; color: var(--mark-grey); }
  .envelope-c4 .side-lockup .slogan { font-size: 6px; color: var(--mark-grey); margin-top: 2px; }
</style>
</head>
<body>

  <section class="piece card card-front" aria-label="Business card front">
    <div class="brand-dot"></div>
    <div class="brand-name">Tolvarin</div>
    <div class="slogan">Measurable Marketing.</div>
  </section>

  <section class="piece card card-back" aria-label="Business card back">
    <div class="brand-dot"></div>
    <div class="contact">
      <div class="company">Company Name</div>
      <div>M: xxx xxx xxxx</div>
      <div>E: info@tolvarin.com.au</div>
      <div class="web">www.tolvarin.com.au</div>
    </div>
  </section>

  <section class="piece envelope-dl" aria-label="DL envelope">
    <div class="brand-dot"></div>
    <div class="brand-name">Tolvarin</div>
    <div class="slogan">Measurable Marketing. Epic Results.</div>
    <div class="contact-line">
      <span>Company Name</span>
      <span>M: xxx xxx xxxx</span>
      <span>E: info@tolvarin.com.au</span>
      <span class="web">www.tolvarin.com.au</span>
    </div>
  </section>

  <section class="piece letterhead" aria-label="Letterhead">
    <div class="brand-dot"></div>
    <div class="brand-name">Tolvarin</div>
    <div class="slogan">Measurable Marketing. Epic Results.</div>
    <div class="watermark" role="img" aria-label="Faint brand mark watermark"></div>
    <div class="contact-line">
      <span>Company Name</span>
      <span>M: xxx xxx xxxx</span>
      <span>E: info@tolvarin.com.au</span>
      <span class="web">www.tolvarin.com.au</span>
    </div>
  </section>

  <section class="piece envelope-c4" aria-label="C4 envelope">
    <div class="flap">
      <svg width="417" height="120" viewBox="0 0 417 120" style="position:absolute;left:0;top:0">
        <path d="M0 0 H417 V90 A30 30 0 0 0 387 120 H30 A30 30 0 0 0 0 90 Z" fill="var(--ink)"/>
      </svg>
      <div class="brand-dot"></div>
      <div class="brand-name">Tolvarin</div>
      <div class="slogan">Measurable Marketing. Epic Results.</div>
    </div>
    <div class="side-mark"></div>
    <div class="side-lockup">
      <div class="brand-name">Tolvarin</div>
      <div class="slogan">Measurable Marketing. Epic Results.</div>
    </div>
  </section>

</body>
</html>
```